Buch-/eBook-Cover für Sachbuch gesucht
Zielgruppe
We're selfpublishing nonfiction books. Interested are adults - mostly man (age range: 25-50) - who want to learn more about leadership at their workplaces.
Aufgabenstellung
The design should be clean and simple, title easy to read, good color contrast (the cover has to stand out from an white background).

```html
<!DOCTYPE html>
<html lang="en">
<head>
<meta charset="utf-8">
<title>Leadership – Book Cover</title>
<link href="https://fonts.googleapis.com/css2?family=Roboto+Condensed:wght@500;700&display=swap" rel="stylesheet">
<style>
  :root {
    --page-bg: #ececec;
    --cover-dark: #0b0f1a;
    --cover-navy: #111a30;
    --cover-blue: #173f7c;
    --text-light: #f3f3f3;
  }
  html, body {
    margin: 0;
    padding: 0;
    width: 1200px;
    height: 1200px;
    overflow: hidden;
    background: var(--page-bg);
  }
  .canvas {
    position: relative;
    width: 1200px;
    height: 1200px;
  }
  .book-cover {
    position: absolute;
    left: 211px;
    top: 50px;
    width: 778px;
    height: 1100px;
    background: var(--cover-dark);
    overflow: hidden;
  }
  .cover-art {
    position: absolute;
    inset: 0;
    background: linear-gradient(150deg,
      var(--cover-navy) 0%,
      var(--cover-dark) 30%,
      var(--cover-blue) 62%,
      var(--cover-navy) 80%,
      var(--cover-dark) 100%);
  }
  .cover-text {
    position: absolute;
    left: 0;
    right: 0;
    margin: 0;
    text-align: center;
    color: var(--text-light);
    font-family: "Roboto Condensed", "Arial Narrow", sans-serif;
    line-height: 1;
    white-space: nowrap;
    transform-origin: center top;
  }
  .title {
    top: 245px;
    font-weight: 700;
    font-size: 156px;
    transform: scaleX(0.81);
  }
  .subtitle {
    top: 396px;
    font-weight: 700;
    font-size: 41px;
    transform: scaleX(0.74);
  }
  .author {
    top: 1023px;
    font-weight: 700;
    font-size: 27px;
    transform: scaleX(0.83);
  }
</style>
</head>
<body>
<div class="canvas">
  <div class="book-cover">
    <div class="cover-art" role="img" aria-label="Abstract dark navy background with soft diagonal blue light"></div>
    <h1 class="cover-text title">LEADERSHIP</h1>
    <p class="cover-text subtitle">FOSTERING GROWTH AND INSPIRING EXCELLENCE</p>
    <p class="cover-text author">DANIEL REXFORD</p>
  </div>
</div>
</body>
</html>
```